Drifting Lantern Coffee Co menu

We would like our existing menu tidied up.
we want to keep the all the items, but need it less busy and clearer to read.

Also want to leave a bit of space to add a few item in the future.

```html
<!DOCTYPE html>
<html lang="en">
<head>
<meta charset="utf-8">
<title>Drifting Lantern Coffee Co — Menu</title>
<link rel="stylesheet" href="https://fonts.googleapis.com/css2?family=Oswald:wght@400&family=Montserrat:wght@400;600;700&family=Rye&display=swap">
<style>
:root{
  --backdrop:#dcdcd2;
  --page:#ffffff;
  --paper:#e3e1d6;
  --ink:#161412;
  --ink-soft:#3a3632;
  --rust:#7b2a17;
  --pill-dark:#111111;
  --pill-rust:#8a3520;
  --leaf-a:#4f7a55;
  --leaf-b:#a9c3a3;
  --berry:#a3302a;
}
*{margin:0;padding:0;box-sizing:border-box}
html,body{width:1200px;height:968px;overflow:hidden;background:var(--backdrop)}
body{position:relative;font-family:"Montserrat",sans-serif;color:var(--ink)}

.menu-page{position:absolute;top:146px;width:492px;height:676px;background:var(--page);overflow:hidden}
.menu-page--hot{left:93px}
.menu-page--cold{left:630px}

.paper-band{position:absolute;left:0;right:0;bottom:0;background:var(--paper)}
.menu-page--hot .paper-band{top:512px}
.menu-page--cold .paper-band{top:362px}

.foliage{position:absolute;border-radius:50%;opacity:.55;
  background:radial-gradient(ellipse at center,var(--leaf-a) 0%,var(--leaf-b) 55%,rgba(169,195,163,0) 75%)}
.foliage--berries{background:radial-gradient(ellipse at center,var(--berry) 0%,var(--leaf-a) 35%,var(--leaf-b) 60%,rgba(169,195,163,0) 78%)}

.brand{position:absolute;left:27px;top:30px;display:flex;align-items:center;gap:8px;
  font-family:"Rye",serif;font-size:17px;line-height:1.15;color:var(--ink)}
.brand-dot{width:14px;height:14px;border-radius:50%;background:var(--ink);flex:none}

.page-title{position:absolute;font-family:"Rye",serif;color:var(--ink);text-align:center;line-height:1}
.page-title .main{display:block;font-size:30px;letter-spacing:1px}
.page-title .sub{display:block;font-size:15px;margin-top:4px}
.menu-page--hot .page-title{left:262px;top:40px;width:170px}
.menu-page--cold .page-title{left:130px;top:26px;width:232px}

.section-title{position:absolute;font-family:"Oswald",sans-serif;font-size:23px;color:var(--rust);line-height:1;letter-spacing:.3px}

.item{position:absolute}
.row{display:flex;align-items:baseline;font-size:8.2px;font-weight:600;letter-spacing:.2px;text-transform:uppercase;white-space:nowrap}
.row .lead{flex:1;border-bottom:1px dotted var(--ink-soft);margin:0 3px;transform:translateY(-2px);min-width:6px}
.row .price{font-size:9px;font-weight:400;text-transform:none}
.desc{font-size:6.4px;line-height:1.28;color:var(--ink-soft);margin-top:2px}
.desc b{font-weight:700;color:var(--ink)}
.sizes{display:flex;gap:2px;margin-top:4px}
.pill{font-size:6px;font-weight:600;color:#fff;background:var(--pill-dark);padding:2px 6px;border-radius:6px;line-height:1.1}
.pill--mid{background:var(--pill-rust)}

.col-left{left:50px;width:161px}
.col-tea{left:262px;width:162px}
.col-ice{left:50px;width:160px}
.col-shake{left:264px;width:158px}

.rule{position:absolute;height:1px;background:#8a8680}

.extras-title{font-size:7.6px;font-weight:600;text-transform:uppercase}
.extras-list{font-size:6.4px;text-transform:uppercase;line-height:1.3;margin-top:5px;color:var(--ink-soft)}
.extras-price{font-size:8px;color:var(--rust);margin-top:6px;font-weight:600}

.special{position:absolute;left:40px;right:40px;text-align:center}
.special-name{display:inline-flex;align-items:center;gap:5px;font-size:7.8px;font-weight:700;color:var(--rust);text-transform:uppercase;letter-spacing:.2px}
.special-name .pill{font-size:5.8px}
.special-desc{font-size:6.3px;line-height:1.3;color:var(--ink-soft);margin-top:4px}

.specialty-title{position:absolute;left:0;right:0;top:396px;text-align:center;font-family:"Rye",serif;font-size:21px;color:var(--ink)}
</style>
</head>
<body>

<!-- Hot drinks page -->
<section class="menu-page menu-page--hot">
  <div class="paper-band"></div>

  <div class="foliage" style="left:425px;top:-20px;width:90px;height:110px" role="img" aria-label="Watercolour coffee leaves"></div>
  <div class="foliage" style="left:-14px;top:190px;width:30px;height:60px" role="img" aria-label="Watercolour coffee leaf"></div>
  <div class="foliage" style="left:-14px;top:395px;width:34px;height:110px" role="img" aria-label="Watercolour coffee leaves"></div>
  <div class="foliage foliage--berries" style="left:350px;top:400px;width:160px;height:170px" role="img" aria-label="Coffee branch with leaves and red cherries"></div>
  <div class="foliage foliage--berries" style="left:-20px;top:550px;width:90px;height:140px" role="img" aria-label="Coffee branch with leaves and red cherries"></div>

  <div class="brand"><span class="brand-dot"></span><span>Drifting Lantern<br>Coffee Co</span></div>
  <div class="page-title"><span class="main">COFFEE</span><span class="sub">&amp; TEA</span></div>

  <h2 class="section-title" style="left:49px;top:122px">COFFEE</h2>

  <div class="item col-left" style="top:151px">
    <div class="row">Flat White<span class="lead"></span><span class="price">$5.00</span></div>
    <p class="desc">Espresso shot with a steamed milk.</p>
    <div class="sizes"><span class="pill">Small $5</span><span class="pill pill--mid">Medium $6</span><span class="pill">Large $7</span></div>
  </div>
  <div class="item col-left" style="top:193px">
    <div class="row">Cappuccino<span class="lead"></span><span class="price">$5.00</span></div>
    <p class="desc">Espresso shot with steamed milk, a<br>thick layer of milk foam and<br>chocolate powder topping</p>
    <div class="sizes"><span class="pill">Small $5</span><span class="pill pill--mid">Medium $6</span><span class="pill">Large $7</span></div>
  </div>
  <div class="item col-left" style="top:250px">
    <div class="row">Latte<span class="lead"></span><span class="price">$5.00</span></div>
    <p class="desc">Espresso shot with steamed milk<br>and a thin layer of milk foam</p>
    <div class="sizes"><span class="pill">Small $5</span><span class="pill pill--mid">Medium $6</span><span class="pill">Large $7</span></div>
  </div>
  <div class="item col-left" style="top:299px">
    <div class="row">Mocha<span class="lead"></span><span class="price">$5.00</span></div>
    <p class="desc">Espresso shot, Belgian chocolate<br>RAW natural infusion with a<br>medium layer of milk foam.</p>
    <div class="sizes"><span class="pill">Small $5</span><span class="pill pill--mid">Medium $6</span><span class="pill">Large $7</span></div>
  </div>
  <div class="item col-left" style="top:358px">
    <div class="row">Americano<span class="lead"></span><span class="price">$5.00</span></div>
    <p class="desc"><b>Americano</b> - Espresso shot topped<br>up with hot water.<br><b>Long Black</b> - Hot water topped off<br>with espresso shot</p>
    <div class="sizes"><span class="pill">Small $5</span><span class="pill pill--mid">Medium $6</span><span class="pill">Large $7</span></div>
  </div>
  <div class="item col-left" style="top:425px">
    <div class="row">Espresso<span class="lead"></span><span class="price">$3.00</span></div>
    <p class="desc">Double espresso shot</p>
  </div>
  <div class="item col-left" style="top:453px">
    <div class="row">Filter / Batch Brew Coffee<span class="lead"></span><span class="price">$4.00</span></div>
    <div class="sizes"><span class="pill">Small $4</span><span class="pill pill--mid">Medium $4</span><span class="pill">Large $4</span></div>
  </div>

  <h2 class="section-title" style="left:262px;top:122px">TEA / OTHER DRINKS</h2>

  <div class="item col-tea" style="top:152px">
    <div class="row">Organic Green Tea<span class="lead"></span><span class="price">$5.00</span></div>
    <div class="sizes"><span class="pill">Small $5</span><span class="pill pill--mid">Medium $6</span><span class="pill">Large $7</span></div>
  </div>
  <div class="item col-tea" style="top:188px">
    <div class="row">English Breakfast Tea<span class="lead"></span><span class="price">$5.00</span></div>
    <div class="sizes"><span class="pill">Small $5</span><span class="pill pill--mid">Medium $6</span><span class="pill">Large $7</span></div>
  </div>
  <div class="item col-tea" style="top:224px">
    <div class="row">Organic Earl Grey Tea<span class="lead"></span><span class="price">$5.00</span></div>
    <div class="sizes"><span class="pill">Small $5</span><span class="pill pill--mid">Medium $6</span><span class="pill">Large $7</span></div>
  </div>
  <div class="item col-tea" style="top:260px">
    <div class="row">Hot Chocolate<span class="lead"></span><span class="price">$5.00</span></div>
    <div class="sizes"><span class="pill">Small $5</span><span class="pill pill--mid">Medium $6</span><span class="pill">Large $7</span></div>
  </div>
  <div class="item col-tea" style="top:295px">
    <div class="row">Dark Cacoa Hot Chocolate<span class="lead"></span><span class="price">$5.00</span></div>
    <div class="sizes"><span class="pill">Small $5</span><span class="pill pill--mid">Medium $6</span><span class="pill">Large $7</span></div>
  </div>
  <div class="item col-tea" style="top:331px">
    <div class="row">Chai Latte<span class="lead"></span><span class="price">$5.00</span></div>
    <div class="sizes"><span class="pill">Small $5</span><span class="pill pill--mid">Medium $6</span><span class="pill">Large $7</span></div>
  </div>

  <div class="rule" style="left:262px;top:369px;width:161px"></div>

  <div class="item col-tea" style="top:382px">
    <p class="extras-title">Raw Natural Infusions</p>
    <p class="extras-list">Caramel, Vanilla, Chai Spice,<br>Hazelnut, Belgian Chocolate</p>
    <p class="extras-price">$5.00</p>
  </div>
  <div class="item col-tea" style="top:437px">
    <p class="extras-title">Milks</p>
    <p class="extras-list">Full Cream, Skinny, Oat,<br>Almond, Soy</p>
    <p class="extras-price">$5.00</p>
  </div>

  <div class="special" style="top:544px">
    <div class="special-name">Honey Brewed Chai <span class="pill">$7.00</span></div>
    <p class="special-desc">Our Honey Chai is handmade and blended in Western Australia. It is made from the finest black tea leaves<br>available, aromatic freshly ground spices and infused with locally sourced raw honey.<br>Served with a choice of steamed milk</p>
  </div>
  <div class="special" style="top:599px">
    <div class="special-name">Colombian Cacoa Salted Caramel Hot Chocolate <span class="pill">$7.00</span></div>
    <p class="special-desc">Made with deep toned and rich cocoa sourced from ancient cocao growing regions of Colombia and<br>sweetened with just enough organic unrefined Colombian panela, all balanced perfectly with a caramel<br>RAW natural infusion and pink Himalayan rock salt. Served with a choice of steamed milk</p>
  </div>
</section>

<!-- Cold drinks page -->
<section class="menu-page menu-page--cold">
  <div class="paper-band"></div>

  <div class="foliage" style="left:-18px;top:-18px;width:75px;height:65px" role="img" aria-label="Watercolour coffee leaves"></div>
  <div class="foliage" style="left:455px;top:-12px;width:50px;height:80px" role="img" aria-label="Watercolour coffee leaves"></div>
  <div class="foliage foliage--berries" style="left:450px;top:230px;width:60px;height:300px" role="img" aria-label="Coffee branch with leaves and red cherries"></div>
  <div class="foliage" style="left:-16px;top:330px;width:40px;height:140px" role="img" aria-label="Watercolour coffee leaves"></div>
  <div class="foliage foliage--berries" style="left:-16px;top:540px;width:50px;height:140px" role="img" aria-label="Coffee branch with leaves and red cherries"></div>

  <div class="page-title"><span class="main">ICED COFFEE</span><span class="sub">&amp; Milkshakes</span></div>

  <h2 class="section-title" style="left:50px;top:101px">ICED COFFEE</h2>
  <div class="item col-ice" style="top:130px">
    <div class="row">Iced Latte<span class="lead"></span><span class="price">$7.50</span></div>
    <p class="desc">Add icecream + $1.00</p>
  </div>
  <div class="item col-ice" style="top:158px">
    <div class="row">Iced Mocha<span class="lead"></span><span class="price">$8.00</span></div>
    <p class="desc">Add icecream + $1.00</p>
  </div>
  <div class="item col-ice" style="top:185px">
    <div class="row">Iced Americano<span class="lead"></span><span class="price">$6.00</span></div>
  </div>
  <div class="item col-ice" style="top:205px">
    <div class="row">Cold Brew<span class="lead"></span><span class="price">$7.50</span></div>
  </div>

  <div class="rule" style="left:50px;top:240px;width:159px"></div>

  <h2 class="section-title" style="left:50px;top:257px">OTHER DRINKS</h2>
  <div class="item col-ice" style="top:288px">
    <div class="row">Iced Chocolate<span class="lead"></span><span class="price">$7.00</span></div>
  </div>
  <div class="item col-ice" style="top:309px">
    <div class="row">Iced Chai<span class="lead"></span><span class="price">$7.00</span></div>
  </div>
  <div class="item col-ice" style="top:331px">
    <div class="row">Puppycino<span class="lead"></span><span class="price">$2.00</span></div>
  </div>

  <h2 class="section-title" style="left:264px;top:101px">MILKSHAKES</h2>
  <div class="item col-shake" style="top:129px">
    <p class="extras-title" style="text-transform:none;font-size:7.6px;line-height:1.25">Milkshake with a choice of chilled<br>milk and ice cream</p>
  </div>
  <div class="item col-shake" style="top:160px"><div class="row">Chocolate<span class="lead"></span><span class="price">$8.00</span></div></div>
  <div class="item col-shake" style="top:182px"><div class="row">Vanilla<span class="lead"></span><span class="price">$8.00</span></div></div>
  <div class="item col-shake" style="top:207px"><div class="row">Caramel<span class="lead"></span><span class="price">$8.00</span></div></div>
  <div class="item col-shake" style="top:232px"><div class="row">Strawberry<span class="lead"></span><span class="price">$8.00</span></div></div>
  <div class="item col-shake" style="top:258px"><div class="row">Mango<span class="lead"></span><span class="price">$8.00</span></div></div>
  <div class="item col-shake" style="top:284px"><div class="row">Banana<span class="lead"></span><span class="price">$8.00</span></div></div>
  <div class="item col-shake" style="top:308px"><div class="row">Cookies &amp; Cream<span class="lead"></span><span class="price">$8.00</span></div></div>
  <div class="item col-shake" style="top:330px"><div class="row">Hazelcrème Milkshake<span class="lead"></span><span class="price">$9.00</span></div></div>

  <h2 class="specialty-title">Specialty Drinks</h2>

  <div class="special" style="top:443px">
    <div class="special-name">Bakehouse Spice Iced Coffee <span class="pill">$9.00</span></div>
    <p class="special-desc">A double shot of espresso extracted over spiced biscuit spread poured over Meadowvale premium extra<br>creamy milk and ice cream. Topped off with whipped cream and crushed spiced biscuits</p>
  </div>
  <div class="special" style="top:495px">
    <div class="special-name">Malt Crunch Iced Coffee <span class="pill">$9.00</span></div>
    <p class="special-desc">A double shot of espresso extracted over melted malt crunch balls. Poured over Meadowvale premium extra creamy<br>milk and ice cream. Topped off with whipped cream and more crushed malt crunch</p>
  </div>
  <div class="special" style="top:547px">
    <div class="special-name">Hazelcrème Iced Coffee <span class="pill">$9.00</span></div>
    <p class="special-desc">A double shot of espresso extracted over melted hazelnut spread. Poured over Meadowvale premium extra creamy milk<br>and ice cream. Topped off with whipped cream and more hazelnut sauce and crushed hazelnuts</p>
  </div>
  <div class="special" style="top:599px">
    <div class="special-name">Colombian Cacoa Salted Caramel Milkshake <span class="pill">$9.00</span></div>
    <p class="special-desc">Made with deep toned and rich cocoa sourced from ancient cocao growing regions of Colombia and<br>sweetened with just enough organic unrefined Colombian panela, all balanced perfectly with a caramel<br>RAW natural infusion and pink Himalayan rock salt. All blended together with icecream and a choice of milk</p>
  </div>
</section>

</body>
</html>
```